Counselling practice needs a Business Card Design

I need a business card design for a new counselling practice in Canberra, Australia. The name of the practice is Dr Neil Hartwood, Counselling Services and the practice focuses on philosophical, narrative and existential counselling for individuals, couples and families. The final design should communicate professionalism, sophistication of analysis and psychological wholeness. The reverse side of the card should have an appointment reminder
Updates

Could the following qualifications also be included on card. BSc (Psychology), BA hons (Philosophy), PhD (Philosophy), Diploma of Community Counselling And the following affiliation Guidance and Wellbeing Society of Tarrin and Districts Inc. (GAWSOT) And my contact phone mobile phone number is 0478315942, and email is Neil.Hartwood347@mailbrook.example for inclusion as well.

Thank you all who have put in a design so far. I just wanted to clarify some design points based on what you have submitted. 1. The Guidance and Wellbeing Society. Tarrin and Districts Inc. (GAWSOT) is an affiliation only. 'Member of the Guidance and Wellbeing Society. Tarrin and Districts Inc (GAWSOT)' should appear with the same prominence of a qualification. 2. The Post Graduate Diploma in Community Counselling is a quaification and should appear as 'PG Dip (Community Counselling)' after the other qualifications. 3. I am advertising myself as a counsellor so 'Dr Neil Hartwood, Counselling Services' or 'Dr Neil Hartwood, Counsellor' is the equivalent of the business name. After looking at some of the designs I prefer Dr Neil Hartwood in sentence case rather than all capitals (DR NEIL HARTWOOD). 4. 'Philosophical, narrative and existential counselling for individuals, couples and families' is the description of the type of counselling services and should appear on the card.

One further point. I have updated my email address for the card. It is now drneilhartwood@tarringuidance.example

```html
<!DOCTYPE html>
<html lang="en">
<head>
<meta charset="utf-8">
<title>Dr Neil Hartwood – Business Card</title>
<link rel="stylesheet" href="https://fonts.googleapis.com/css2?family=Arimo:wght@400;700&display=swap">
<style>
  :root {
    --backdrop: #1f1f21;
    --card: #5b5b60;
    --ink: #2c2c30;
    --ink-soft: #333337;
  }
  * { margin: 0; padding: 0; box-sizing: border-box; }
  html, body {
    width: 1200px;
    height: 621px;
    overflow: hidden;
    background: var(--backdrop);
    font-family: "Arimo", "Helvetica Neue", Arial, sans-serif;
    color: var(--ink);
  }
  .canvas { position: relative; width: 1200px; height: 621px; }
  .card {
    position: absolute;
    top: 166px;
    width: 504px;
    height: 286px;
    background: var(--card);
    text-align: center;
  }
  .card--front { left: 60px; }
  .card--back { left: 628px; }
  .card p, .card .reminder-fields { position: absolute; left: 0; right: 0; line-height: 1; white-space: nowrap; }

  .practice-name { font-weight: 700; letter-spacing: 0.5px; color: var(--ink); }
  .card--front .practice-name { top: 58px; font-size: 40px; }
  .service-line { font-size: 14px; color: var(--ink-soft); }
  .service-line--1 { top: 114px; }
  .service-line--2 { top: 133px; }

  .reminder-title { top: 186px; font-size: 12px; font-weight: 700; letter-spacing: 1px; text-transform: uppercase; color: var(--ink); }
  .reminder-fields {
    top: 214px;
    display: flex;
    justify-content: center;
    gap: 28px;
    font-size: 13px;
    color: var(--ink-soft);
  }
  .reminder-field { display: flex; align-items: flex-end; gap: 8px; }
  .reminder-blank { display: inline-block; width: 120px; border-bottom: 1px solid var(--ink); height: 13px; }

  .card--back .practice-name { top: 36px; font-size: 28px; }
  .role { top: 72px; font-size: 13px; color: var(--ink-soft); }
  .qualifications { top: 118px; font-size: 9.5px; color: var(--ink-soft); }
  .membership { top: 134px; font-size: 9.5px; color: var(--ink-soft); }
  .phone { top: 196px; font-size: 19px; color: var(--ink); }
  .email { top: 226px; font-size: 17px; color: var(--ink); }
</style>
</head>
<body>
<main class="canvas">
  <section class="card card--front" aria-label="Card front">
    <p class="practice-name">Dr Neil Hartwood</p>
    <p class="service-line service-line--1">Philosophical, narrative and existential counselling</p>
    <p class="service-line service-line--2">for individuals, couples and families</p>
    <p class="reminder-title">Appointment reminder</p>
    <div class="reminder-fields">
      <span class="reminder-field">Date <span class="reminder-blank"></span></span>
      <span class="reminder-field">Time <span class="reminder-blank"></span></span>
    </div>
  </section>

  <section class="card card--back" aria-label="Card back">
    <p class="practice-name">Dr Neil Hartwood</p>
    <p class="role">Counsellor</p>
    <p class="qualifications">BSc (Psychology), BA hons (Philosophy), PhD (Philosophy), PG Dip (Community Counselling)</p>
    <p class="membership">Member of the Guidance and Wellbeing Society. Tarrin and Districts Inc (GAWSOT)</p>
    <p class="phone">0478315942</p>
    <p class="email">drneilhartwood@tarringuidance.example</p>
  </section>
</main>
</body>
</html>
```